Web Developer Needs a Business Card Design

I need a personal business card design that represents me as a web developer for potential employers. I would like the background to be a dark color on the front for contrast with my logo and name. The back will have all my information along with a smaller version of the logo. I want something with a modern look and feel, not too conservative. This will be used for potential employers and freelance work.

Industry/Entity Type

Business

Contact Information for Business Card

Front should have my logo and name. The back should have all my personal information which would include: name: Tom Varulek, phone: 570-614-3098, email: tomvarulek@quillbox.net, website url: www.tomvarulek.net, logo, web developer.

Font styles to use
Sans Serif

Requirements
Must have
• Must include my logo. The color palette base color will be the logo color.

```html
<!DOCTYPE html>
<html lang="en">
<head>
<meta charset="utf-8">
<title>Tom Varulek – Business Card</title>
<link rel="stylesheet" href="https://fonts.googleapis.com/css2?family=Source+Sans+3:wght@400;600;700&display=swap">
<style>
  :root {
    --backdrop: #000000;
    --card: #323437;
    --card-deep: #2c2e31;
    --accent: #5ec4a8;
    --accent-soft: rgba(94, 196, 168, 0.35);
    --ink-light: #f2f2f2;
  }
  * { margin: 0; padding: 0; box-sizing: border-box; }
  html, body {
    width: 1200px;
    height: 900px;
    overflow: hidden;
    background: var(--backdrop);
    font-family: "Source Sans 3", sans-serif;
  }
  .canvas { position: relative; width: 1200px; height: 900px; }
  .card {
    position: absolute;
    top: 271px;
    width: 457px;
    height: 281px;
    border-radius: 14px;
    background: linear-gradient(180deg, var(--card) 0%, var(--card-deep) 100%);
    overflow: hidden;
  }
  .card--info { left: 137px; }
  .card--front { left: 626px; }

  .brand-mark {
    position: absolute;
    display: flex;
    align-items: center;
    gap: 8px;
    color: var(--accent);
    font-weight: 600;
    line-height: 1;
    white-space: nowrap;
  }
  .brand-mark__dot {
    display: block;
    width: 14px;
    height: 14px;
    border-radius: 50%;
    background: var(--accent);
  }
  .card--info .brand-mark { left: 113px; top: 140px; transform: translate(-50%, -50%); font-size: 26px; }
  .card--front .brand-mark { left: 50%; top: 110px; transform: translate(-50%, -50%); font-size: 32px; }
  .card--front .brand-mark__dot { width: 16px; height: 16px; }

  .divider {
    position: absolute;
    left: 218px;
    top: 80px;
    width: 1px;
    height: 140px;
    background: linear-gradient(180deg, transparent, var(--accent-soft) 20%, var(--accent-soft) 80%, transparent);
  }

  .identity { position: absolute; left: 251px; top: 88px; }
  .identity__name { color: var(--accent); font-size: 17px; font-weight: 700; line-height: 1.1; }
  .identity__role { color: var(--ink-light); font-size: 13px; line-height: 1.2; }

  .contact-list { position: absolute; left: 253px; top: 146px; list-style: none; }
  .contact-list li {
    display: flex;
    align-items: center;
    gap: 6px;
    color: var(--ink-light);
    font-size: 13px;
    height: 19px;
  }
  .contact-list svg { width: 9px; height: 9px; fill: var(--accent); flex: none; }

  .front-name {
    position: absolute;
    left: 0; right: 0;
    top: 182px;
    text-align: center;
    color: var(--ink-light);
    font-size: 22px;
    font-weight: 600;
    letter-spacing: 0.5px;
  }
  .front-role {
    position: absolute;
    left: 0; right: 0;
    top: 213px;
    text-align: center;
    color: var(--accent);
    font-size: 14.5px;
  }
</style>
</head>
<body>
<main class="canvas">
  <section class="card card--info" aria-label="Contact side">
    <div class="brand-mark"><span class="brand-mark__dot"></span>Varulek</div>
    <div class="divider"></div>
    <div class="identity">
      <p class="identity__name">Tom Varulek</p>
      <p class="identity__role">Front-End Developer</p>
    </div>
    <ul class="contact-list">
      <li>
        <svg viewBox="0 0 10 10" aria-hidden="true"><path d="M2 0.5 L3.6 2.6 L2.8 3.6 C3.4 4.9 5 6.5 6.4 7.2 L7.4 6.4 L9.5 8 L8.4 9.5 C4.5 9.2 0.8 5.5 0.5 1.6 Z"/></svg>
        570-614-3098
      </li>
      <li>
        <svg viewBox="0 0 10 10" aria-hidden="true"><path d="M0.5 2 H9.5 V8.5 H0.5 Z M1 2.4 L5 5.6 L9 2.4" fill="var(--accent)"/><path d="M1 2.6 L5 5.6 L9 2.6" fill="none" stroke="#323437" stroke-width="0.8"/></svg>
        tomvarulek@quillbox.net
      </li>
      <li>
        <svg viewBox="0 0 10 10" aria-hidden="true"><g fill="none" stroke="var(--accent)" stroke-width="1.3" stroke-linecap="round"><path d="M4.2 5.8 L5.8 4.2"/><path d="M3.2 4.8 L1.8 6.2 A1.4 1.4 0 0 0 3.8 8.2 L5.2 6.8"/><path d="M6.8 5.2 L8.2 3.8 A1.4 1.4 0 0 0 6.2 1.8 L4.8 3.2"/></g></svg>
        www.tomvarulek.net
      </li>
    </ul>
  </section>

  <section class="card card--front" aria-label="Front side">
    <div class="brand-mark"><span class="brand-mark__dot"></span>Varulek</div>
    <h1 class="front-name">TOM VARULEK</h1>
    <p class="front-role">Front-End Developer</p>
  </section>
</main>
</body>
</html>
```